Request for Business Card Design

Hi. My name is Marlene, I am looking for a new business card design for my company, Quarrow Signal Instruments, LLC. I really like the design you did for Tarsel Venture and was hoping you could do something similar using our full logo and our mark. I am also open to any raised texture design using our mark. I have attached our full logo, which would need to be somewhere on the card, as well as the mark in both outline and full form, as well as our brand colors / guide. The card does not have to be white, as long as our logo and mark appear. I actually like darker colored business cards more, but am open to all options. If you are interested in working with me, please let me know. We would also take the business card design into letterhead design if you can do that.

```html
<!DOCTYPE html>
<html lang="en">
<head>
<meta charset="utf-8">
<title>Quarrow Signal Instruments – Business Card</title>
<link href="https://fonts.googleapis.com/css2?family=Montserrat:wght@400;500;700&display=swap" rel="stylesheet">
<style>
  :root {
    --stage: #e9e9eb;
    --charcoal: #47474a;
    --paper: #ffffff;
    --brand-blue: #1596c2;
    --ink: #2b2b2d;
  }
  * { box-sizing: border-box; margin: 0; padding: 0; }
  html, body { width: 1200px; height: 880px; overflow: hidden; }
  body {
    background: var(--stage);
    font-family: 'Montserrat', sans-serif;
    display: flex;
    flex-direction: column;
    align-items: center;
    justify-content: center;
    gap: 40px;
  }
  .card {
    position: relative;
    width: 640px;
    height: 366px;
    overflow: hidden;
    box-shadow: 0 6px 18px rgba(0,0,0,.18);
  }
  .card--front { background: var(--charcoal); }
  .card--back { background: var(--paper); }

  .brand {
    position: absolute;
    display: flex;
    align-items: center;
    gap: 16px;
  }
  .brand__dot {
    flex: none;
    border-radius: 50%;
    background: var(--brand-blue);
  }
  .brand__name {
    font-weight: 700;
    text-transform: uppercase;
    letter-spacing: .04em;
    line-height: 1.1;
  }
  .card--front .brand { left: 50%; top: 50%; transform: translate(-50%, -50%); }
  .card--front .brand__dot { width: 64px; height: 64px; }
  .card--front .brand__name { color: var(--paper); font-size: 30px; }

  .card--back .brand { left: 46px; top: 160px; }
  .card--back .brand__dot { width: 40px; height: 40px; }
  .card--back .brand__name { color: var(--charcoal); font-size: 17px; }

  .wave { position: absolute; inset: 0; }

  .divider {
    position: absolute;
    left: 336px;
    top: 60px;
    width: 2px;
    height: 150px;
    background: var(--brand-blue);
  }
  .contact {
    position: absolute;
    left: 356px;
    top: 56px;
    color: var(--ink);
  }
  .contact__name {
    font-weight: 700;
    font-size: 20px;
    text-transform: uppercase;
    color: var(--ink);
  }
  .contact__name .first { color: var(--brand-blue); }
  .contact__role { font-size: 14px; margin: 2px 0 12px; }
  .contact__list { list-style: none; }
  .contact__item {
    display: flex;
    align-items: center;
    gap: 9px;
    font-size: 13.5px;
    margin-bottom: 6px;
  }
  .contact__item svg { width: 15px; height: 15px; flex: none; fill: var(--brand-blue); }
</style>
</head>
<body>

<section class="card card--front">
  <div class="brand">
    <span class="brand__dot"></span>
    <span class="brand__name">Quarrow Signal<br>Instruments</span>
  </div>
</section>

<section class="card card--back">
  <svg class="wave" viewBox="0 0 640 366" preserveAspectRatio="none" aria-hidden="true">
    <path d="M0 306 C 200 316 320 300 420 268 C 510 240 570 230 640 228 L640 366 L0 366 Z" fill="var(--charcoal)"/>
    <path d="M110 300 C 250 300 330 276 420 250 C 500 228 560 218 630 214 C 560 224 500 236 420 258 C 330 284 250 304 110 300 Z" fill="var(--brand-blue)"/>
  </svg>

  <div class="brand">
    <span class="brand__dot"></span>
    <span class="brand__name">Quarrow Signal<br>Instruments</span>
  </div>

  <div class="divider"></div>

  <div class="contact">
    <p class="contact__name"><span class="first">Tovin</span> Hale</p>
    <p class="contact__role">Owner</p>
    <ul class="contact__list">
      <li class="contact__item">
        <svg viewBox="0 0 24 24"><path d="M6.6 10.8a15 15 0 0 0 6.6 6.6l2.2-2.2a1 1 0 0 1 1-.25 11.4 11.4 0 0 0 3.6.57 1 1 0 0 1 1 1V20a1 1 0 0 1-1 1A17 17 0 0 1 3 4a1 1 0 0 1 1-1h3.5a1 1 0 0 1 1 1c0 1.25.2 2.45.57 3.57a1 1 0 0 1-.25 1z"/></svg>
        555.014.2286
      </li>
      <li class="contact__item">
        <svg viewBox="0 0 24 24"><path d="M2 5h20v14H2z M2 5l10 8 10-8" fill="var(--brand-blue)" stroke="#fff" stroke-width="1.4"/></svg>
        info@quarrowsignal.com
      </li>
      <li class="contact__item">
        <svg viewBox="0 0 24 24"><circle cx="12" cy="12" r="10"/><path d="M2 12h20M12 2c3 3 3 17 0 20M12 2c-3 3-3 17 0 20" fill="none" stroke="#fff" stroke-width="1.3"/></svg>
        www.quarrowsignal.com
      </li>
    </ul>
  </div>
</section>

</body>
</html>
```